Business Card For Halvenmoor Financial Consulting

Hi, I would like a business card designed. Bold, modern.
Please use the same design as the logo. I have also attached the website design to see the overall theme.
Wordmark Font
Color: Hex: #01AEF7

```html
<!DOCTYPE html>
<html lang="en">
<head>
<meta charset="UTF-8">
<title>Halvenmoor Financial Consulting — Business Card</title>
<link href="https://fonts.googleapis.com/css2?family=Source+Sans+3:wght@400;600;700&display=swap" rel="stylesheet">
<style>
  :root {
    --page: #e4e4e4;
    --card: #13212a;
    --brand: #36a3d9;
    --white: #ffffff;
    --text: #e8eef2;
    --pattern-silver: #7f8c95;
    --pattern-mid: #2a3842;
    --pattern-dark: #0e1920;
  }
  * { margin: 0; padding: 0; box-sizing: border-box; }
  html, body {
    width: 1200px; height: 960px; overflow: hidden;
    background: radial-gradient(ellipse at center, #f2f2f2 0%, var(--page) 75%);
    font-family: "Source Sans 3", "Source Sans Pro", Arial, sans-serif;
  }
  .card {
    position: absolute; left: 296px; width: 609px; height: 348px;
    background: var(--card); overflow: hidden;
    box-shadow: 3px 4px 6px rgba(0,0,0,.28);
  }
  .card--front { top: 109px; }
  .card--back { top: 511px; }

  .pattern-area {
    position: absolute; inset: 0;
    background:
      radial-gradient(ellipse 60% 75% at 0% 0%, rgba(127,140,149,.55) 0%, rgba(127,140,149,0) 100%),
      linear-gradient(105deg, var(--pattern-mid) 0%, #1c2a33 45%, var(--pattern-dark) 100%);
  }

  .brand {
    position: absolute; display: flex; align-items: center;
  }
  .brand__square {
    border: 3px solid var(--brand); flex: none;
  }
  .brand__name {
    color: var(--white); font-weight: 700; text-transform: uppercase;
    line-height: 1.12; letter-spacing: .06em; white-space: nowrap;
  }
  .card--front .brand { left: 146px; top: 148px; gap: 12px; }
  .card--front .brand__square { width: 52px; height: 52px; }
  .card--front .brand__name { font-size: 20px; }

  .card--back .brand { left: 41px; top: 40px; gap: 10px; }
  .card--back .brand__square { width: 43px; height: 43px; }
  .card--back .brand__name { font-size: 17px; }

  .contact-person { position: absolute; left: 41px; top: 129px; }
  .contact-person__name { color: var(--brand); font-weight: 700; font-size: 19px; line-height: 1.2; }
  .contact-person__role { color: var(--text); font-size: 15px; margin-top: 1px; }

  .contact-list { position: absolute; left: 41px; top: 199px; list-style: none; }
  .contact-list li {
    display: flex; align-items: flex-start; gap: 6px;
    color: var(--text); font-size: 15px; line-height: 21px;
  }
  .contact-list li + li { margin-top: 7px; }
  .contact-list li.tight { margin-top: 4px; }
  .contact-list svg { width: 13px; height: 13px; margin-top: 4px; flex: none; }

  .web-band {
    position: absolute; left: 0; top: 304px; width: 374px; height: 17px;
    background: var(--brand);
    color: var(--white); font-weight: 700; font-size: 14px; line-height: 17px;
    padding-left: 41px;
  }
  .graphic-area {
    position: absolute; left: 374px; top: 69px; width: 206px; height: 252px;
    background: linear-gradient(180deg, rgba(54,163,217,.25) 0%, rgba(54,163,217,.7) 100%);
  }
</style>
</head>
<body>

<section class="card card--front">
  <div class="pattern-area" role="img" aria-label="Decorative repeated brand pattern fading from silver at top left to dark at bottom right"></div>
  <div class="brand">
    <span class="brand__square"></span>
    <span class="brand__name">Halvenmoor<br>Financial Consulting</span>
  </div>
</section>

<section class="card card--back">
  <div class="brand">
    <span class="brand__square"></span>
    <span class="brand__name">Halvenmoor<br>Financial Consulting</span>
  </div>

  <div class="contact-person">
    <p class="contact-person__name">Daniel Whitcombe</p>
    <p class="contact-person__role">President</p>
  </div>

  <ul class="contact-list">
    <li>
      <svg viewBox="0 0 14 14" fill="none" stroke="#36a3d9" stroke-width="1.4"><path d="M7 13s-4.5-4.6-4.5-7.6a4.5 4.5 0 0 1 9 0C11.5 8.4 7 13 7 13z"/><circle cx="7" cy="5.4" r="1.6"/></svg>
      <span>418 Larkfield Avenue, Suite 210<br>Ashbury, CA 95012</span>
    </li>
    <li>
      <svg viewBox="0 0 14 14" fill="none" stroke="#36a3d9" stroke-width="1.4"><path d="M3 1.5h2.3l1 3-1.5 1a7 7 0 0 0 3.7 3.7l1-1.5 3 1v2.3c0 .6-.5 1-1 1A11 11 0 0 1 2 2.5c0-.6.4-1 1-1z"/></svg>
      <span>555-201-3847</span>
    </li>
    <li class="tight">
      <svg viewBox="0 0 14 14" fill="none" stroke="#36a3d9" stroke-width="1.4"><rect x="1" y="3" width="12" height="8.5"/><path d="M1 3l6 5 6-5"/></svg>
      <span>daniel@halvenmoor.com</span>
    </li>
  </ul>

  <div class="web-band">www.halvenmoor.com</div>
  <div class="graphic-area" role="img" aria-label="Large brand graphic in blue rising from the web address band"></div>
</section>

</body>
</html>
```